Business Card Design

I need business cards designed for a new company i have started that makes cakes, particularly themed kids cakes with a really modern design and I would like to have my business cards reflect this. I have attached some photos of cakes I have made and would like some to be used.

Industry/Entity Type

Business

Contact Information for Business Card

Business Name: Tarts and Treats by Maren
Mobile: 0492 815 063
email: maren@tartsandtreatsbymaren.example.au
Instagram: instagram.com/tartsandtreatsbymaren/
Facebook: fb.me/tartsandtreatsbymaren

Colors
e667a6
b768aa
3276b5

Requirements
Must have
• Business Name: Tarts and Treats by Maren
• Mobile: 0492 815 063
• email: maren@tartsandtreatsbymaren.example.au
• Instagram: instagram.com/tartsandtreatsbymaren/
• Facebook: fb.me/tartsandtreatsbymaren
Nice to have
• 2 to 3 pictures of my cakes

```html
<!DOCTYPE html>
<html lang="en">
<head>
<meta charset="utf-8">
<title>Tarts and Treats by Maren — Business Card</title>
<link rel="stylesheet" href="https://fonts.googleapis.com/css2?family=Open+Sans:wght@400;600;700&display=swap">
<style>
  :root {
    --pink: #e667a6;
    --plum: #b768aa;
    --blue: #3276b5;
    --blue-deep: #235f98;
    --ink: #5a5a5a;
    --paper: #ffffff;
    --backdrop: #e9e6e1;
  }
  * { box-sizing: border-box; margin: 0; padding: 0; }
  html, body {
    width: 1200px; height: 843px; overflow: hidden;
    background: var(--backdrop);
    font-family: "Open Sans", Arial, sans-serif;
  }
  .sheet {
    width: 1200px; height: 843px;
    display: flex; align-items: center; justify-content: center; gap: 40px;
  }
  .card {
    position: relative;
    width: 540px; height: 309px;
    overflow: hidden;
    box-shadow: 0 10px 28px rgba(0,0,0,.22);
  }
  /* back */
  .card--back {
    background: linear-gradient(135deg, #4a8ccb 0%, var(--blue) 45%, var(--blue-deep) 100%);
    display: flex; align-items: center; justify-content: center;
  }
  .brand {
    display: flex; align-items: center; gap: 14px;
    font-weight: 600; line-height: 1.05;
  }
  .brand__dot { width: 22px; height: 22px; border-radius: 50%; flex: none; }
  .brand__name { display: block; }
  .card--back .brand { color: var(--paper); font-size: 34px; }
  .card--back .brand__dot { background: var(--paper); }
  /* front */
  .card--front { background: var(--paper); }
  .card--front .brand {
    position: absolute; right: 34px; top: 58px;
    color: var(--pink); font-size: 25px; text-align: left;
  }
  .card--front .brand__dot { background: var(--pink); width: 18px; height: 18px; }
  .person { position: absolute; left: 34px; top: 118px; }
  .person__name {
    color: var(--pink); font-weight: 600; font-size: 16px;
    letter-spacing: .5px; text-transform: uppercase;
  }
  .person__role { color: var(--pink); font-size: 12px; margin-top: 1px; }
  .contacts { list-style: none; margin-top: 10px; }
  .contacts li {
    display: flex; align-items: center; gap: 9px;
    color: var(--ink); font-size: 12.5px; line-height: 20px;
  }
  .contacts svg { width: 12px; height: 12px; flex: none; }
  .contacts .marker {
    width: 10px; height: 10px; margin: 0 1px; flex: none;
    background: var(--pink); border-radius: 2px;
  }
  .footer-band { position: absolute; left: 0; bottom: 0; width: 540px; height: 22px; }
</style>
</head>
<body>
<main class="sheet">
  <section class="card card--back" aria-label="Card back">
    <div class="brand">
      <span class="brand__dot"></span>
      <span class="brand__name">Tarts and Treats<br>by Maren</span>
    </div>
  </section>

  <section class="card card--front" aria-label="Card front">
    <div class="brand">
      <span class="brand__dot"></span>
      <span class="brand__name">Tarts and Treats<br>by Maren</span>
    </div>

    <div class="person">
      <p class="person__name">Elias Brandt</p>
      <p class="person__role">CEO/Founder</p>
      <ul class="contacts">
        <li>
          <svg viewBox="0 0 12 12" aria-hidden="true"><rect x="2.5" y="0.5" width="7" height="11" rx="1.2" fill="none" stroke="var(--pink)" stroke-width="1.2"/><circle cx="6" cy="9.6" r=".7" fill="var(--pink)"/></svg>
          0492 815 063
        </li>
        <li>
          <svg viewBox="0 0 12 12" aria-hidden="true"><rect x="0.5" y="2" width="11" height="8" rx="1" fill="var(--pink)"/><path d="M1 2.6 6 6.6 11 2.6" fill="none" stroke="#fff" stroke-width="1"/></svg>
          maren@tartsandtreatsbymaren.example.au
        </li>
        <li><span class="marker"></span>tartsandtreatsbymaren</li>
        <li><span class="marker"></span>tartsandtreatsbymaren</li>
      </ul>
    </div>

    <svg class="footer-band" viewBox="0 0 540 22" preserveAspectRatio="none" aria-hidden="true">
      <defs>
        <linearGradient id="pinkBand" x1="0" x2="1">
          <stop offset="0" stop-color="var(--pink)"/>
          <stop offset="1" stop-color="#ef9cc5"/>
        </linearGradient>
      </defs>
      <polygon points="0,12 300,8 300,22 0,22" fill="url(#pinkBand)"/>
      <polygon points="306,8 540,4 540,22 296,22" fill="var(--blue)"/>
    </svg>
  </section>
</main>
</body>
</html>
```